Business Card Design Project

Business Card
We are rebranding with a new logo
Industry/Entity Type
Business
Contact Information for Business Card
Dennis Morvale +61 487215963 dennis@quorv.com.au P.O. Box 872 Fernlow QLD 4309
Requirements
Must have
- Logo

```html
<!DOCTYPE html>
<html lang="en">
<head>
<meta charset="utf-8">
<title>Quorv International – Business Card</title>
<link rel="stylesheet" href="https://fonts.googleapis.com/css2?family=Source+Sans+3:wght@400;600;700&display=swap">
<style>
  :root {
    --stage: #3a3b3d;
    --card-white: #f7f8f8;
    --brand-blue: #1a8cc0;
    --brand-blue-deep: #0e6f9c;
    --brand-orange: #ef8c1f;
    --ink-light: #ffffff;
    --shadow: rgba(0, 0, 0, 0.35);
  }
  * { margin: 0; padding: 0; box-sizing: border-box; }
  html, body {
    width: 1200px; height: 960px; overflow: hidden;
    background: var(--stage);
    font-family: "Source Sans 3", "Myriad Pro", Arial, sans-serif;
  }
  .canvas {
    width: 1200px; height: 960px;
    display: flex; flex-direction: column;
    align-items: center; justify-content: center; gap: 48px;
  }
  .card {
    position: relative;
    width: 640px; height: 366px;
    border-radius: 4px; overflow: hidden;
    box-shadow: 0 14px 30px var(--shadow);
  }

  /* Back of card */
  .card--back {
    background: var(--brand-orange);
    display: flex; flex-direction: column;
    align-items: center; justify-content: center;
    color: var(--ink-light);
  }
  .back-brand { display: flex; align-items: center; gap: 14px; }
  .brand-dot {
    width: 22px; height: 22px; border-radius: 50%;
    background: var(--ink-light);
  }
  .back-brand .brand-name {
    font-size: 46px; font-weight: 600; letter-spacing: 2px; line-height: 1;
    color: var(--ink-light);
  }
  .back-web {
    margin-top: 34px;
    font-size: 14px; letter-spacing: 4px;
  }

  /* Front of card */
  .card--front { background: var(--card-white); }
  .front-wave {
    position: absolute; inset: 0; width: 100%; height: 100%;
  }
  .front-brand {
    position: absolute; left: 56px; top: 56px;
    display: flex; align-items: flex-start; gap: 14px;
  }
  .front-brand .brand-dot { background: var(--brand-blue); margin-top: 10px; }
  .front-brand .brand-name {
    font-size: 40px; font-weight: 600; letter-spacing: 2px; line-height: 1.05;
    color: var(--brand-blue);
  }
  .contact {
    position: absolute; right: 30px; bottom: 18px;
    list-style: none; text-align: right;
    color: var(--ink-light);
    font-size: 15px; line-height: 20px;
  }
  .contact li { display: flex; justify-content: flex-end; align-items: center; gap: 8px; }
  .contact .contact-name {
    font-weight: 700; font-size: 17px; letter-spacing: 0.5px;
    text-transform: uppercase; margin-bottom: 2px; padding-right: 22px;
  }
  .contact .icon { width: 14px; height: 14px; flex: none; }
  .contact .no-icon { padding-right: 22px; }
</style>
</head>
<body>
<main class="canvas">

  <section class="card card--back" aria-label="Card back">
    <div class="back-brand">
      <span class="brand-dot"></span>
      <span class="brand-name">QUORV INTERNATIONAL</span>
    </div>
    <p class="back-web">www.quorv.com.au</p>
  </section>

  <section class="card card--front" aria-label="Card front">
    <svg class="front-wave" viewBox="0 0 640 366" preserveAspectRatio="none" aria-hidden="true">
      <path d="M0,214 C170,290 420,292 640,100 L640,366 L0,366 Z" fill="var(--brand-blue-deep)"/>
      <path d="M0,222 C170,298 420,300 640,108 L640,366 L0,366 Z" fill="var(--brand-blue)"/>
    </svg>

    <div class="front-brand">
      <span class="brand-dot"></span>
      <span class="brand-name">QUORV<br>INTERNATIONAL</span>
    </div>

    <ul class="contact">
      <li class="contact-name">Dennis Morvale</li>
      <li>+61 487215963
        <svg class="icon" viewBox="0 0 16 16" aria-hidden="true"><path fill="#fff" d="M4 1.5l2.2 2.6-1.3 1.6c.8 1.8 2.3 3.3 4.1 4.1l1.6-1.3 2.6 2.2-1.4 2.3C6.6 12.6 3.4 9.4 1.7 4.2z"/></svg>
      </li>
      <li>dennis@quorv.com.au
        <svg class="icon" viewBox="0 0 16 16" aria-hidden="true"><rect x="1" y="3.5" width="14" height="9" rx="1" fill="#fff"/><path d="M1.5 4l6.5 5 6.5-5" fill="none" stroke="#1a8cc0" stroke-width="1.2"/></svg>
      </li>
      <li>www.quorv.com.au
        <svg class="icon" viewBox="0 0 16 16" aria-hidden="true"><circle cx="8" cy="8" r="6.5" fill="#fff"/><path d="M1.5 8h13M8 1.5c-2.5 3-2.5 10 0 13M8 1.5c2.5 3 2.5 10 0 13" fill="none" stroke="#1a8cc0" stroke-width="1"/></svg>
      </li>
      <li class="no-icon">P.O. Box 872, Fernlow QLD 4309</li>
    </ul>
  </section>

</main>
</body>
</html>
```